We (R. T. Galvin & Partners, Inc.) are an executive Search firm based in Los Angeles that is exclusively focused in the Med Tech and Health Tech arenas.   I need a logo to communicate that we are a high end search firm, but also that we are focused in the medicine and science arenas called health tech and med tech.  Many of our clients have robotics and artificial intelligence type products, so it is very technology forward.  I tend to gravitate towards clean, sharp aesthetic as opposed to something that is really over the top.
Attached are files with my logo in two different layouts.  In addition to the letterhead and envelope, I also will need an electronic letterhead in Microsoft Word.  I tend to
I look forward to seeing the designs and just let me know if you have any questions.
Dale

```html
<!DOCTYPE html>
<html lang="en">
<head>
<meta charset="utf-8">
<title>R. T. Galvin &amp; Partners, Inc. — Stationery</title>
<link href="https://fonts.googleapis.com/css2?family=Raleway:wght@300;400;600&family=Roboto:wght@400&display=swap" rel="stylesheet">
<style>
  :root {
    --backdrop: #6b6b6b;
    --paper: #f4f4f4;
    --paper-edge: #c9c9c9;
    --ink: #111111;
    --body-ink: #6a6a6a;
    --brand-blue: #4fa3dc;
    --rule-blue: #1a95d3;
    --flap-edge: #2f5f80;
  }
  * { margin: 0; padding: 0; box-sizing: border-box; }
  html, body { width: 1200px; height: 993px; overflow: hidden; }
  body { background: var(--backdrop); position: relative; font-family: "Raleway", sans-serif; }

  .pattern-sheet {
    position: absolute; left: 244px; top: 50px; width: 562px; height: 530px;
    background: linear-gradient(135deg, var(--brand-blue), #5aa9de 50%, var(--brand-blue));
    box-shadow: 0 1px 3px rgba(0,0,0,0.35);
  }

  .letterhead {
    position: absolute; left: 83px; top: 99px; width: 562px; height: 790px;
    background: var(--paper);
    border: 1px solid var(--paper-edge);
    box-shadow: 0 1px 4px rgba(0,0,0,0.4);
  }
  .brand { position: absolute; display: flex; align-items: center; gap: 12px; }
  .brand-dot { border-radius: 50%; background: var(--brand-blue); flex: none; }
  .brand-name { font-weight: 600; color: var(--ink); text-transform: uppercase; line-height: 1.15; }
  .letterhead .brand { left: 48px; top: 72px; }
  .letterhead .brand-dot { width: 44px; height: 44px; }
  .letterhead .brand-name { font-size: 24px; letter-spacing: 0.5px; }
  .letterhead .brand-name small { display: block; font-size: 13px; letter-spacing: 3.5px; }

  .divider { position: absolute; left: 193px; top: 162px; width: 1px; height: 387px; background: #333; }
  .divider-accent { position: absolute; left: 192px; top: 549px; width: 3px; height: 142px; background: var(--rule-blue); border-radius: 2px; }

  .contact { position: absolute; right: 395px; top: 560px; font-family: "Roboto", sans-serif; font-size: 10px; color: var(--ink); text-align: right; }
  .contact li { list-style: none; line-height: 13.6px; display: flex; justify-content: flex-end; align-items: center; gap: 8px; white-space: nowrap; }
  .contact .gap { margin-top: 10px; }
  .contact svg { width: 8px; height: 8px; fill: var(--brand-blue); flex: none; }
  .contact .blank { width: 8px; }

  .letter { position: absolute; left: 216px; top: 176px; width: 302px; font-size: 11px; font-weight: 300; color: var(--body-ink); line-height: 13.6px; text-align: justify; }
  .letter p { margin-bottom: 13.6px; }
  .letter .salutation { margin-bottom: 27px; }
  .letter .closing { margin-top: 27px; }

  .envelope {
    position: absolute; background: var(--paper);
    border: 1px solid var(--paper-edge);
    box-shadow: -2px 2px 6px rgba(0,0,0,0.35), 0 0 1px rgba(0,0,0,0.4);
  }
  .envelope-front { left: 514px; top: 250px; width: 574px; height: 277px; }
  .envelope-front .brand { left: 40px; top: 34px; gap: 9px; }
  .envelope-front .brand-dot { width: 26px; height: 26px; }
  .envelope-front .brand-name { font-size: 15px; }
  .envelope-front .brand-name small { display: block; font-size: 7.5px; letter-spacing: 2px; }
  .return-address { position: absolute; left: 87px; top: 69px; font-size: 10px; font-style: normal; color: var(--ink); line-height: 12px; }

  .envelope-back { left: 511px; top: 576px; width: 574px; height: 277px; }
  .flap { position: absolute; left: -1px; top: -1px; width: 574px; height: 97px; overflow: visible; }
  .flap-name { position: absolute; left: 0; top: 40px; width: 572px; text-align: center; font-size: 11px; font-weight: 600; letter-spacing: 2px; color: #ffffff; text-transform: uppercase; }
</style>
</head>
<body>

  <div class="pattern-sheet" role="img" aria-label="Blue sheet with a repeating light-blue decorative pattern"></div>

  <section class="letterhead">
    <div class="brand">
      <span class="brand-dot"></span>
      <div class="brand-name">R. T. Galvin<small>&amp; Partners Inc.</small></div>
    </div>

    <div class="divider"></div>
    <div class="divider-accent"></div>

    <ul class="contact">
      <li>R.T. Galvin &amp; Partners Inc <svg viewBox="0 0 8 8"><path d="M4 0a3 3 0 0 0-3 3c0 2.2 3 5 3 5s3-2.8 3-5a3 3 0 0 0-3-3zm0 4.2a1.2 1.2 0 1 1 0-2.4 1.2 1.2 0 0 1 0 2.4z"/></svg></li>
      <li>4120 Cedar Crest Way <span class="blank"></span></li>
      <li>Juneau <span class="blank"></span></li>
      <li>Alaska 34611 <span class="blank"></span></li>
      <li class="gap">555-214-7730 <svg viewBox="0 0 8 8"><path d="M1.6 0.3l1.3 1.6-.8 1a5 5 0 0 0 3 3l1-.8 1.6 1.3-.9 1.2C3.6 7.4.6 4.4.4 1.2z"/></svg></li>
      <li>555-318-6042 <svg viewBox="0 0 8 8"><path d="M2 0h4v8H2zM2.8.8v5.6h2.4V.8z"/></svg></li>
      <li>555-406-1189 <svg viewBox="0 0 8 8"><path d="M2 0h4v2H2zM0 2.6h8v3.6H6.5V8h-5V6.2H0zM2.2 5.4v1.8h3.6V5.4z"/></svg></li>
      <li>info@rtgalvin-partners.com <svg viewBox="0 0 8 8"><path d="M0 1.5h8v5H0zm.8.6L4 4.4l3.2-2.3z"/></svg></li>
      <li>rtgalvin-partners.com <svg viewBox="0 0 8 8"><circle cx="4" cy="4" r="4"/></svg></li>
    </ul>

    <div class="letter">
      <p class="salutation">Dear Mr. Harlow,</p>
      <p>Lorem ipsum dolor sit amet, consectetur adipiscing elit. Donec orci purus, luctus vitae dignissim eu, tincidunt sed leo. Vivamus faucibus, ipsum nec aliquet viverra, nunc nisl condimentum ligula, sit amet sagittis enim ligula a ligula. Nam egestas tortor id nisi porttitor mattis. In tortor magna, sodales suscipit a, tempus non massa. Vivamus et lorem ut lorem vel massa nulla. Phasellus nec eros mauris, ut faucibus orci.</p>
      <p>Donec malesuada orci vitae nulla accumsan sed mattis massa. Quisque accumsan iaculis magna et tristique velit. Maecenas consequat, magna eget tincidunt dictum, nibh rutrum mi, id feugiat ante nisi eu risus. Nunc pretium orci, rhoncus a placerat in, ultricies in mi. Cras vel lacus eros, vel fringilla nisi suscipit eget. Quisque sed elit mattis nulla at porttitor.</p>
      <p>Sed id augue vitae urna euismod commodo aliquet a quam. Pellentesque arcu velit, cursus et malesuada ut, consequat et diam. Nullam erat sem, rhoncus id ullamcorper vitae, tempus et arcu. In ultricies ultricies nulla, ut rutrum lorem porta a. Donec eu magna a metus ornare faucibus. Morbi sed dapibus ultricies. Morbi semper, est id tincidunt lacinia, arcu adipiscing lacus, ac bibendum nulla leo quis nunc. Atque nec diam sed risus consectetur a commodo orci nibh. Vestibulum id purus lorem.</p>
      <p>It is a long established fact that a reader will be distracted by the readable content of a page when looking at its layout. The point of using Lorem Ipsum is that it has a more-or-less normal distribution of letters, as opposed to using 'Content here, content here', making it look like readable English. Many desktop publishing packages</p>
      <p class="closing">Sincerely,</p>
    </div>
  </section>

  <section class="envelope envelope-front">
    <div class="brand">
      <span class="brand-dot"></span>
      <div class="brand-name">R. T. Galvin<small>&amp; Partners Inc.</small></div>
    </div>
    <address class="return-address">4120 Cedar Crest Way<br>Juneau, Alaska 34611</address>
  </section>

  <section class="envelope envelope-back">
    <svg class="flap" viewBox="0 0 574 97" aria-hidden="true">
      <path d="M0 0H574L561 68Q556 95 528 95H46Q18 95 13 68Z" fill="var(--brand-blue)" stroke="var(--flap-edge)" stroke-width="1.5"/>
    </svg>
    <div class="flap-name">R. T. Galvin &amp; Partners Inc.</div>
  </section>

</body>
</html>
```